Postcard design to acquire new clients for my Property Management Company

I'm looking for a postcard design that I can send to prospective clients detailing information about my company and services.
Postcard should be eye catching and contain information from www.bramblecrestpm.com. I've provided a few screen shots for the most important information and my logo.
Target Market(s)
Real Estate
Industry/Entity Type
Real Estate
Font styles to use
Sans Serif
Requirements
Must have
- Must be eye catching!! this will be a direct mail piece - I'd like for the card to be read and not tossed in the trash immediately.
Design que from the logo.
A place to write / print the receipts name and address.
our physical address - 2387 Hollow Pine Road, Lubbock, TX 79852.
Should not have
- the contact information on the business card is not accurate - please use info from website.

```html
<!DOCTYPE html>
<html lang="en">
<head>
<meta charset="utf-8">
<title>Bramblecrest Property Management – Postcard</title>
<link rel="stylesheet" href="https://fonts.googleapis.com/css2?family=Montserrat:wght@300;400;500;600;700;800&display=swap">
<style>
:root{
  --blue:#0f4c85;
  --blue-deep:#0b3b6b;
  --gray:#9b9b9b;
  --gray-text:#6b6b6b;
  --light:#f1f2f4;
  --stage:#d6d8dc;
  --white:#ffffff;
}
*{margin:0;padding:0;box-sizing:border-box}
html,body{width:933px;height:1200px;overflow:hidden}
body{background:var(--stage);font-family:"Montserrat",sans-serif;position:relative}
.card{position:absolute;left:79px;width:759px;overflow:hidden;background:var(--light)}
.card--front{top:75px;height:505px}
.card--back{top:617px;height:507px;background:var(--white)}
.shapes{position:absolute;inset:0;width:100%;height:100%}
.abs{position:absolute}
.brand-name{font-weight:700;color:var(--blue);letter-spacing:5px;line-height:1;white-space:nowrap}
.brand-sub{font-weight:700;color:var(--blue);letter-spacing:4.6px;line-height:1;white-space:nowrap}
.front .brand-name{font-size:33px}
.headline{font-weight:800;color:var(--blue);font-size:24px;line-height:30px;letter-spacing:.2px}
.lede{font-weight:400;color:var(--gray-text);font-size:17px;line-height:22px}
.contact-title{font-weight:800;color:var(--blue);font-size:21px}
.call-label{font-weight:400;color:var(--gray-text);font-size:15px}
.phone{font-weight:700;color:var(--blue);font-size:19px}
.email{font-weight:400;color:var(--gray-text);font-size:15.5px}
.address{font-weight:400;color:var(--gray-text);font-size:11.5px;white-space:nowrap}
.web{font-weight:400;color:var(--white);font-size:12px;letter-spacing:1.1px;white-space:nowrap}
.services-title{font-weight:800;color:var(--blue);font-size:24px;line-height:29px}
.services-lede{font-weight:400;color:var(--gray-text);font-size:15px;line-height:19px}
.service{position:absolute;width:90px;text-align:center;color:var(--gray-text);font-size:11.5px;line-height:14px}
.service svg{display:block;margin:0 auto 4px;width:24px;height:24px;fill:var(--blue)}
.choose{font-weight:800;color:var(--white);font-size:15.5px;line-height:18.5px}
.back-call{color:var(--white);font-size:11px}
.back-phone{color:var(--white);font-weight:700;font-size:13.5px}
.back-email{color:var(--white);font-size:11px}
.return-address{font-weight:400;color:var(--gray-text);font-size:9.5px;line-height:13px;white-space:nowrap}
.plan{position:absolute;background:var(--white);text-align:center;padding-top:7px;box-shadow:0 0 3px rgba(0,0,0,.15)}
.plan__name{font-weight:700;color:var(--blue);font-size:8.5px}
.plan__tag{color:var(--gray-text);font-size:5.5px;margin-top:1px}
.plan__rate{font-weight:700;color:var(--blue);font-size:16px;margin-top:3px}
.plan__unit{font-size:4.8px;color:#444;margin-top:1px}
.plan__list{list-style:none;font-size:4.8px;color:#444;line-height:13.4px;margin-top:2px}
.stamp{position:absolute;left:668px;top:29px;width:77px;height:77px;border:1px solid var(--gray)}
</style>
</head>
<body>

<!-- Front of postcard -->
<section class="card card--front front">
  <svg class="shapes" viewBox="0 0 759 505" aria-hidden="true">
    <defs>
      <linearGradient id="photoTone" x1="0" y1="0" x2="1" y2="1">
        <stop offset="0" stop-color="#5f6a6f"/>
        <stop offset=".5" stop-color="#7d8b8f"/>
        <stop offset="1" stop-color="#4c5559"/>
      </linearGradient>
    </defs>
    <polygon points="400,235 470,235 330,505 300,505" fill="var(--gray)" opacity=".85"/>
    <polygon points="555,0 594,0 394,505 350,505" fill="var(--blue)"/>
    <polygon points="594,0 759,0 759,505 394,505" fill="url(#photoTone)"/>
    <polygon points="580,0 640,0 560,192 497,192" fill="var(--gray)" opacity=".55"/>
    <polygon points="0,466 337,466 326,489 0,489" fill="var(--blue)"/>
    <line x1="231" y1="475" x2="727" y2="475" stroke="var(--gray)" stroke-width="1"/>
  </svg>
  <div class="abs" role="img" aria-label="Photo of a person in a striped shirt handing over a house key" style="left:394px;top:0;width:365px;height:505px;clip-path:polygon(200px 0,365px 0,365px 505px,0 505px)"></div>

  <div class="abs" style="left:43px;top:57px">
    <div class="brand-name">BRAMBLECREST</div>
    <div class="brand-sub" style="font-size:19px;margin-top:10px">PROPERTY MANAGEMENT</div>
  </div>

  <h1 class="abs headline" style="left:43px;top:170px">PROPERTY MANAGEMENT<br>ACROSS LUBBOCK, TX</h1>
  <p class="abs lede" style="left:43px;top:249px">Maximize your financial<br>returns with support from<br>our rental specialists</p>

  <h2 class="abs contact-title" style="left:43px;top:345px">Contact Our Team</h2>
  <p class="abs call-label" style="left:43px;top:378px">Call Now:</p>
  <p class="abs phone" style="left:43px;top:395px">(806) 555-0147</p>
  <p class="abs email" style="left:43px;top:418px">info@bramblecrestpm.com</p>
  <p class="abs address" style="left:43px;top:442px">2387 Hollow Pine Road, Lubbock, TX 79852</p>
  <p class="abs web" style="left:43px;top:470px">www.bramblecrestpm.com</p>
</section>

<!-- Back of postcard -->
<section class="card card--back">
  <svg class="shapes" viewBox="0 0 759 507" aria-hidden="true">
    <polygon points="0,0 352,0 470,302 0,302" fill="var(--light)"/>
    <polygon points="300,0 352,0 480,302 450,302" fill="var(--gray)" opacity=".7"/>
    <polygon points="352,0 394,0 558,507 0,507 0,302 470,302" fill="var(--blue)"/>
    <polygon points="300,0 352,0 470,302 440,302" fill="var(--gray)" opacity=".6"/>
    <polygon points="390,140 420,140 470,270 440,270" fill="var(--gray)" opacity=".7"/>
    <polygon points="498,314 558,314 620,507 558,507" fill="var(--gray)" opacity=".8"/>
    <polygon points="542,473 759,473 759,496 548,496" fill="var(--blue-deep)"/>
    <polygon points="251,30 424,30 424,117 285,117" fill="var(--blue)"/>
  </svg>
  <div class="abs" role="img" aria-label="Photo of two businessmen reviewing documents in a modern office" style="left:276px;top:30px;width:148px;height:87px;background:linear-gradient(135deg,#2f4f76,#8aa4bf 60%,#c9d5df);clip-path:polygon(0 0,100% 0,100% 100%,24% 100%)"></div>

  <h2 class="abs services-title" style="left:35px;top:36px">DISCOVER OUR<br>SERVICES</h2>
  <p class="abs services-lede" style="left:35px;top:101px">We offer full-service property<br>management solutions</p>

  <div class="service" style="left:25px;top:161px">
    <svg viewBox="0 0 24 24"><path d="M12 3 2 12h3v8h5v-5h4v5h5v-8h3z"/></svg>Property<br>Marketing</div>
  <div class="service" style="left:113px;top:161px">
    <svg viewBox="0 0 24 24"><circle cx="8" cy="8" r="4"/><circle cx="17" cy="9" r="3.3"/><path d="M0 20c0-4 3.5-7 8-7s8 3 8 7zM15 20c0-2.5-.8-4.5-2.2-6 1.2-.6 2.6-.9 4.2-.9 3.9 0 7 2.6 7 6.9z"/></svg>Tenant<br>Screening</div>
  <div class="service" style="left:201px;top:161px">
    <svg viewBox="0 0 24 24"><path d="M11 1h2v3c2.5.3 4.3 1.7 4.6 4h-2.6c-.3-1.2-1.5-1.9-3-1.9-1.8 0-2.9.8-2.9 2 0 1.3 1.2 1.7 3.3 2.2 3 .7 5.4 1.7 5.4 4.6 0 2.4-1.900 4-4.8 4.3V23h-2v-3.8c-2.9-.3-4.9-2-5-4.6h2.6c.2 1.5 1.6 2.4 3.5 2.4 1.9 0 3.1-.8 3.1-2.1s-1.1-1.7-3.5-2.300c-2.9-.7-5.100-1.700-5.100-4.400 0-2.200 1.800-3.800 4.400-4.100z"/></svg>Rent<br>Collection</div>
  <div class="service" style="left:288px;top:161px">
    <svg viewBox="0 0 24 24"><path d="M11 2h2v3l7 1v1h-1l3 7c0 2-1.8 3-3.5 3S15 16 15 14l3-7h-1l-4-.6V20h4v2H7v-2h4V6.4L7 7H6l3 7c0 2-1.8 3-3.5 3S2 16 2 14l3-7H4V6l7-1zM5.5 9 3.5 14h4zm13 0-2 5h4z"/></svg>Legal<br>Guidance</div>

  <div class="service" style="left:25px;top:232px">
    <svg viewBox="0 0 24 24"><path d="M14 2l8 8-3 3-2-2-11 11-3-3 11-11-2-2z"/></svg>Maintenance</div>
  <div class="service" style="left:113px;top:232px">
    <svg viewBox="0 0 24 24"><path d="M10 2a8 8 0 0 1 6.3 12.9l5.4 5.4-2 2-5.4-5.4A8 8 0 1 1 10 2zm0 3a5 5 0 1 0 0 10 5 5 0 0 0 0-10z"/></svg>Property<br>Inspections</div>
  <div class="service" style="left:201px;top:232px">
    <svg viewBox="0 0 24 24"><path d="M2 3h2v16h18v2H2zM7 10h2v7H7zm4-4h2v11h-2zm4 6h2v5h-2zm4-3h2v8h-2z"/></svg>Financial<br>Reporting</div>
  <div class="service" style="left:288px;top:232px">
    <svg viewBox="0 0 24 24"><path d="M12 1 3 4.5v6c0 6 3.8 10.6 9 12.5 5.2-1.9 9-6.5 9-12.5v-6zm0 3v15.8c-3.6-1.6-6-5.2-6-9.3V6.6z"/></svg>Evictions</div>

  <h3 class="abs choose" style="left:35px;top:324px">CHOOSE<br>THE RIGHT<br>PROPERTY<br>MANAGEMENT<br>SYSTEM</h3>
  <p class="abs back-call" style="left:35px;top:442px">Call Now:</p>
  <p class="abs back-phone" style="left:35px;top:455px">(806) 555-0147</p>
  <p class="abs back-email" style="left:35px;top:473px">info@bramblecrestpm.com</p>

  <article class="plan" style="left:168px;top:319px;width:104px;height:151px">
    <div class="plan__name">Lease Only</div>
    <div class="plan__tag">- You Just Need Tenants -</div>
    <div class="plan__rate">9%</div>
    <div class="plan__unit">of annual lease</div>
    <ul class="plan__list">
      <li>Professional Photography</li><li>Marketing &amp; Advertising</li><li>Property Showings</li>
      <li>Tenant Screening &amp; Qualifications</li><li>Lease Execution</li><li>Move In Coordination</li>
    </ul>
  </article>
  <article class="plan" style="left:279px;top:313px;width:105px;height:180px">
    <div class="plan__name">Full Service</div>
    <div class="plan__tag">- Our Most Popular -</div>
    <div class="plan__rate">10%</div>
    <div class="plan__unit">of monthly rent</div>
    <ul class="plan__list">
      <li>Includes Leasing Service</li><li>24/7 Emergency Response</li><li>Move In &amp; Out Inspections</li>
      <li>Professional Lease Enforcement</li><li>Schedule &amp; Oversee all Repairs</li><li>Pay all Invoices</li>
      <li>Monthly &amp; Year End Statements</li><li>Annual Market Rent Analysis</li>
    </ul>
  </article>
  <article class="plan" style="left:390px;top:319px;width:105px;height:122px">
    <div class="plan__name">Premium Service</div>
    <div class="plan__tag">- Our Premier Service -</div>
    <div class="plan__rate">12%</div>
    <div class="plan__unit">of monthly rent</div>
    <ul class="plan__list">
      <li>Includes Full Service Features</li><li>Professional Video Marketing</li>
      <li>Home Warranty Coordination</li><li>Tenant Retention Program</li>
    </ul>
  </article>

  <div class="abs" style="left:438px;top:34px">
    <div class="brand-name" style="font-size:21px;letter-spacing:3.4px">BRAMBLECREST</div>
    <div class="brand-sub" style="font-size:11.5px;letter-spacing:2.8px;margin-top:6px">PROPERTY MANAGEMENT</div>
    <p class="return-address" style="margin-top:8px">2387 Hollow Pine Road<br>Lubbock, TX 79852</p>
  </div>
  <div class="stamp" aria-label="Postage stamp area"></div>
  <p class="abs web" style="right:22px;top:477px">www.bramblecrestpm.com</p>
</section>

</body>
</html>
```